Hartwell Estates Business Cards

I would like a business card that includes myself and my partner.
Includes: Logo, office #, email, website, our names, our numbers and possibly the address. I would also like the logo to be embossed and the card to be horizontal.
There is a photo of our yard signs to give you an idea of the colors of our business.

Target Market(s)

Everyone in real estate market.
We are in a rural area. Our clientele are from all socioeconomic backgrounds.

Industry/Entity Type

Real Estate Agent

Contact Information for Business Card

Company Name: Hartwell Estates
Our Names, Titles & Cell #'s : Dana Pembrook-Broker (555).317.6624, Marla Pembrook-Realtor (555).609.1385
Office #: (555).240.3918
Website: hartwellestates-demo.com
Joint Email: pembrook@hartwellestates-demo.com
Office Address: 418B W. Calloway Ave.
Millbrook, KS. 70913

Font styles to use
Serif

Requirements
Must have
• HORIZONTAL, Logo, Myself and my partners names, Our cell #'s, our office #, our website, our email address
Nice to have
• Embossed logo, office address, our titles.

```html
<!DOCTYPE html>
<html lang="en">
<head>
<meta charset="utf-8">
<title>Hartwell Estates Business Cards</title>
<link href="https://fonts.googleapis.com/css2?family=Tinos:wght@400;700&display=swap" rel="stylesheet">
<style>
  :root {
    --purple: #4a2266;
    --white: #ffffff;
    --ink-grey: #4f4f4f;
    --backdrop: #e6e4e2;
    --dot: #5a2f78;
  }
  html, body {
    margin: 0;
    padding: 0;
    width: 1200px;
    height: 1189px;
    overflow: hidden;
    background: var(--backdrop);
  }
  .sheet {
    position: relative;
    width: 1200px;
    height: 1189px;
    font-family: "Tinos", "Times New Roman", serif;
  }
  .card {
    position: absolute;
    left: 220px;
    width: 760px;
    height: 434px;
    box-shadow: 0 6px 18px rgba(0,0,0,0.12);
    overflow: hidden;
  }
  .card-front {
    top: 90px;
    background: var(--purple);
    color: var(--white);
    text-align: center;
  }
  .brand-mark {
    position: absolute;
    left: 0;
    right: 0;
    top: 130px;
    font-size: 72px;
    line-height: 1;
    font-weight: 400;
    letter-spacing: 1px;
  }
  .front-web {
    position: absolute;
    left: 0;
    right: 0;
    top: 320px;
    font-size: 19px;
    letter-spacing: 0.3px;
  }
  .card-back {
    top: 665px;
    background: var(--white);
  }
  .back-brand {
    position: absolute;
    left: 44px;
    top: 150px;
    width: 300px;
    display: flex;
    align-items: center;
    gap: 16px;
    color: var(--purple);
  }
  .back-brand .square {
    width: 34px;
    height: 34px;
    background: var(--purple);
    flex: none;
  }
  .back-brand .name {
    font-size: 44px;
    line-height: 1.05;
    font-weight: 700;
  }
  .details {
    position: absolute;
    left: 370px;
    top: 48px;
    width: 360px;
    font-size: 17px;
    color: var(--ink-grey);
    line-height: 1.2;
  }
  .office-address { font-style: normal; }
  .rule {
    border: 0;
    border-top: 3px dotted var(--dot);
    margin: 10px 0 12px;
  }
  .agent { margin-bottom: 10px; }
  .agent-name {
    font-size: 26px;
    color: var(--purple);
    font-weight: 700;
    line-height: 1.05;
  }
  .agent-title { padding-left: 16px; }
  .agent-phone { padding-left: 32px; }
  .label {
    color: var(--purple);
    font-weight: 700;
  }
</style>
</head>
<body>
<main class="sheet">
  <section class="card card-front" aria-label="Card front">
    <div class="brand-mark">Hartwell Estates</div>
    <div class="front-web">hartwellestates-demo.com</div>
  </section>

  <section class="card card-back" aria-label="Card back">
    <div class="back-brand">
      <span class="square" aria-hidden="true"></span>
      <span class="name">Hartwell Estates</span>
    </div>
    <div class="details">
      <address class="office-address">
        418B W. Calloway Ave.<br>Millbrook, KS. 70913
      </address>
      <hr class="rule">
      <div class="agent">
        <div class="agent-name">Dana Pembrook</div>
        <div class="agent-title">Broker</div>
        <div class="agent-phone"><span class="label">M:</span> (555).317.6624</div>
      </div>
      <div class="agent">
        <div class="agent-name">Marla Pembrook</div>
        <div class="agent-title">Realtor</div>
        <div class="agent-phone"><span class="label">M:</span> (555).609.1385</div>
      </div>
      <hr class="rule">
      <div class="contact"><span class="label">Office:</span> (555).240.3918</div>
      <div class="contact"><span class="label">Email:</span> pembrook@hartwellestates-demo.com</div>
    </div>
  </section>
</main>
</body>
</html>
```